Haulage company, lets use ruby red white and some 3rd color for web design. and Garvel Pryce Transport logo

Target Market(s)

Transport industry

Industry/Entity Type

transport

Number of Pages Required

2 page

Requirements
Must have
• Logo

```html
<!DOCTYPE html>
<html lang="en">
<head>
<meta charset="utf-8">
<title>Garvel Pryce Transport</title>
<link href="https://fonts.googleapis.com/css2?family=Jost:wght@500;600;700&family=Open+Sans:wght@400;600;700&display=swap" rel="stylesheet">
<style>
:root{
  --ruby:#9d1420;
  --ruby-dark:#7e0f19;
  --teal:#14978a;
  --ink:#1d1d1f;
  --night:#1f1f27;
  --black:#0b0b0d;
  --grey:#6a6a6a;
  --white:#ffffff;
  --line:#e4d6d7;
}
*{margin:0;padding:0;box-sizing:border-box}
html,body{width:1200px;height:4843px;overflow:hidden}
body{position:relative;background:var(--white);font-family:"Open Sans",Arial,sans-serif;color:var(--ink)}
h1,h2,h3,.heading{font-family:"Jost","Open Sans",sans-serif;font-weight:600}
.btn{position:absolute;display:flex;align-items:center;justify-content:center;font-family:"Open Sans",Arial,sans-serif;font-weight:700;font-size:15px;border-radius:0 16px 0 16px;text-decoration:none}
.btn-teal{background:var(--teal);color:var(--white)}
.btn-white{background:var(--white);color:var(--teal)}

/* header */
.site-header{position:absolute;left:0;top:0;width:1200px;height:113px;background:var(--white);border-top:4px solid var(--teal)}
.logo{position:absolute;left:113px;top:22px;font-family:"Open Sans",sans-serif;font-weight:700;color:var(--ruby);font-size:24px;line-height:32px;text-transform:uppercase}
.header-cta{left:963px;top:22px;width:122px;height:38px}
.main-nav{position:absolute;top:77px;left:0;width:1200px;font-size:11px;font-weight:700;color:var(--ink)}
.main-nav span{position:absolute}

/* hero */
.hero{position:absolute;left:0;top:113px;width:1200px;height:1194px;background:var(--ruby)}
.hero-photo{position:absolute;left:0;top:0;width:1200px;height:700px;background:linear-gradient(180deg,#9fb2c9 0%,#7f91a8 30%,#5b6470 55%,#4a4d55 100%)}
.hero-wave{position:absolute;left:0;top:480px;width:1200px;height:260px}
.hero-kicker{position:absolute;left:113px;top:110px;color:var(--white);font-size:29px;letter-spacing:.5px}
.hero-title{position:absolute;left:113px;top:152px;color:var(--white);font-family:"Jost",sans-serif;font-weight:700;font-size:72px;line-height:76px;letter-spacing:1px}
.hero-text{position:absolute;left:113px;top:333px;width:500px;color:var(--white);font-size:14.5px;line-height:34px}
.hero-start{left:113px;top:427px;width:133px;height:40px}
.hero-contact{left:277px;top:427px;width:135px;height:40px}

.service-card{position:absolute;top:762px;width:313px;height:342px;background:var(--white);border-radius:0 0 90px 0;padding:14px}
.service-inner{width:100%;height:100%;border:1px solid #c9a3a7;border-radius:0 0 80px 0;background:repeating-linear-gradient(135deg,#fff 0 6px,#f6f6f6 6px 7px);text-align:center;padding-top:56px}
.service-inner svg{display:block;margin:0 auto}
.service-inner h3{font-family:"Open Sans",sans-serif;font-weight:700;font-size:17px;margin-top:16px;color:var(--ink)}
.service-inner p{font-size:11px;line-height:22.5px;color:var(--grey);margin:8px auto 0;width:245px}

/* about */
.about-photo{position:absolute;top:1446px;width:245px;height:473px}
.section-title{font-family:"Jost",sans-serif;font-weight:600;font-size:41px;color:var(--ink);letter-spacing:.5px}
.about-title{position:absolute;left:687px;top:1458px}
.body-copy{font-size:12px;line-height:30px;color:var(--grey)}
.about-copy{position:absolute;left:687px;top:1528px;width:405px}
.about-copy p+p{margin-top:30px}
.about-btn{left:687px;top:1853px;width:137px;height:41px}

/* why choose */
.why{position:absolute;left:0;top:2043px;width:1200px;height:630px;background:linear-gradient(180deg,#c9d4e6 0%,#dde3ee 45%,#7f8a6c 72%,#8d8f92 100%)}
.why-box{position:absolute;left:0;top:113px;width:564px;height:430px;background:var(--white);border-right:8px solid var(--ruby)}
.why-title{position:absolute;left:94px;top:60px}
.why-copy{position:absolute;left:94px;top:128px;width:405px}
.why-btn{left:94px;top:314px;width:137px;height:41px}

/* news */
.news-title{position:absolute;left:0;top:2770px;width:1200px;text-align:center}
.news-sub{position:absolute;left:215px;top:2840px;width:770px;text-align:center;font-size:14.5px;line-height:32px;color:var(--grey)}
.news-photo{position:absolute;top:2938px;width:313px;height:234px}
.news-card{position:absolute;top:3126px;width:287px;height:213px;background:var(--white);border-bottom:3px solid var(--ruby);box-shadow:0 6px 18px rgba(0,0,0,.12);padding:22px 24px}
.news-date{font-size:9.5px;font-weight:700;color:var(--ruby)}
.news-card h3{font-family:"Open Sans",sans-serif;font-weight:700;font-size:11.5px;line-height:22px;margin-top:6px;color:var(--ink)}
.news-card p{font-size:10.5px;line-height:21.5px;color:var(--grey);margin-top:6px}

/* contact */
.contact-wave{position:absolute;left:0;top:3455px;width:1200px;height:140px}
.contact{position:absolute;left:0;top:3560px;width:1200px;height:917px;background:var(--night)}
.contact-title{position:absolute;left:0;top:3565px;width:1200px;text-align:center;color:var(--white);font-size:41px}
.field{position:absolute;background:var(--white);border-radius:4px;font-size:10.5px;color:#444;padding:10px 24px}
.send{position:absolute;left:277px;top:3826px;width:310px;height:38px;background:var(--ruby);color:var(--white);border-radius:4px;font-size:13px;font-weight:700;display:flex;align-items:center;justify-content:center}
.contact-photo{position:absolute;left:0;top:3912px;width:1200px;height:565px;background:linear-gradient(180deg,var(--night) 0%,#3b3a40 30%,#6e6768 60%,#2a2526 88%,var(--black) 100%)}

/* footer */
.site-footer{position:absolute;left:0;top:4477px;width:1200px;height:366px;background:var(--black);color:var(--white)}
.footer-logo{position:absolute;left:113px;top:70px;font-family:"Jost",sans-serif;font-weight:600;font-size:33px;line-height:44px;text-transform:uppercase}
.footer-about{position:absolute;left:113px;top:167px;width:270px;font-size:11px;line-height:26.5px}
.footer-col{position:absolute;top:71px;font-size:11px}
.footer-col h4{font-family:"Open Sans",sans-serif;font-weight:700;font-size:14px;margin-bottom:11px}
.footer-col li{list-style:none;line-height:29.5px}
.footer-rule{position:absolute;left:113px;top:4772px;width:974px;height:1px;background:#2c6f68}
.copyright{position:absolute;left:0;top:4802px;width:1200px;text-align:center;color:var(--white);font-size:10.5px}
</style>
</head>
<body>

<header class="site-header">
  <div class="logo">Garvel Pryce<br>Transport</div>
  <a class="btn btn-teal header-cta">Contact Us</a>
  <nav class="main-nav">
    <span style="left:394px">HOME</span>
    <span style="left:486px">ABOUT US</span>
    <span style="left:602px">OUR SERVICES</span>
    <span style="left:742px">WHY CHOOSE US?</span>
    <span style="left:904px">TESTIMONIALS</span>
    <span style="left:1047px">BLOGS</span>
  </nav>
</header>

<section class="hero">
  <div class="hero-photo" role="img" aria-label="Photo of a refrigerated lorry driving along a coastal road under a cloudy sky"></div>
  <svg class="hero-wave" viewBox="0 0 1200 260" preserveAspectRatio="none" aria-hidden="true">
    <path d="M0,60 Q560,300 1200,72 L1200,260 L0,260 Z" fill="#14978a"/>
    <path d="M0,86 Q560,316 1200,94 L1200,260 L0,260 Z" fill="#9d1420"/>
  </svg>
  <div class="hero-kicker heading">WELCOME TO</div>
  <h1 class="hero-title">GARVEL PRYCE<br>TRANSPORT</h1>
  <p class="hero-text">Sed ut perspiciatis unde omnis iste natus error sit voluptatem accusantium doloremque laudantium, totam rem aperiam, eaque ipsa</p>
  <a class="btn btn-teal hero-start">Get Started</a>
  <a class="btn btn-white hero-contact">Contact Us</a>

  <div class="service-card" style="left:105px">
    <div class="service-inner">
      <svg width="60" height="60" viewBox="0 0 60 60" fill="none" stroke="#9d1420" stroke-width="2.4">
        <circle cx="30" cy="30" r="13"/><circle cx="30" cy="30" r="5"/>
        <path d="M30 10v6M30 44v6M10 30h6M44 30h6M16 16l4 4M40 40l4 4M44 16l-4 4M16 44l4-4" stroke-linecap="round"/>
      </svg>
      <h3>SCHEDULE SERVICE</h3>
      <p>Sed ut perspiciatis unde omnis iste natus error sit voluptatem accusantium doloremque laudantium, totam rem aperiam, eaque ipsa quae ab illo inventore verit</p>
    </div>
  </div>
  <div class="service-card" style="left:444px">
    <div class="service-inner">
      <svg width="60" height="60" viewBox="0 0 60 60" fill="none">
        <path d="M30 6a24 24 0 1 1-22 14" stroke="#9d1420" stroke-width="2.4" stroke-dasharray="5 4" stroke-linecap="round"/>
        <text x="30" y="35" text-anchor="middle" font-family="Open Sans,sans-serif" font-weight="700" font-size="15" fill="#14978a">24/7</text>
      </svg>
      <h3>24/7 SUPPORT</h3>
      <p>Sed ut perspiciatis unde omnis iste natus error sit voluptatem accusantium doloremque laudantium, totam rem aperiam, eaque ipsa quae ab illo inventore verit</p>
    </div>
  </div>
  <div class="service-card" style="left:781px">
    <div class="service-inner">
      <svg width="60" height="60" viewBox="0 0 60 60" fill="none" stroke-width="2.4">
        <path d="M12 30a18 18 0 0 1 36 0" stroke="#9d1420"/>
        <rect x="8" y="28" width="8" height="13" rx="3" stroke="#9d1420"/>
        <rect x="44" y="28" width="8" height="13" rx="3" stroke="#9d1420"/>
        <path d="M20 22h20a3 3 0 0 1 3 3v11a3 3 0 0 1-3 3H30l-6 5v-5h-4a3 3 0 0 1-3-3V25a3 3 0 0 1 3-3z" stroke="#9d1420"/>
        <circle cx="24" cy="30.5" r="1.6" fill="#14978a" stroke="none"/><circle cx="30" cy="30.5" r="1.6" fill="#14978a" stroke="none"/><circle cx="36" cy="30.5" r="1.6" fill="#14978a" stroke="none"/>
      </svg>
      <h3>ACCUSANTIUM DOLORE</h3>
      <p>Sed ut perspiciatis unde omnis iste natus error sit voluptatem accusantium doloremque laudantium, totam rem aperiam, eaque ipsa quae ab illo inventore verit</p>
    </div>
  </div>
</section>

<section>
  <div class="about-photo" style="left:113px;background:linear-gradient(180deg,#8aa2c8 0%,#c9b7a8 45%,#9b2b34 70%,#4a4c52 100%)" role="img" aria-label="Photo of a white and ruby lorry cab parked under a canopy at dusk"></div>
  <div class="about-photo" style="left:382px;background:linear-gradient(180deg,#6d6a72 0%,#d9a55a 35%,#b58a62 55%,#4c4a48 100%)" role="img" aria-label="Photo of a white lorry on a road at sunset"></div>
  <h2 class="section-title about-title">ABOUT US</h2>
  <div class="body-copy about-copy">
    <p>I must explain to you how all this mistaken idea of denouncing pleasure and praising pain was born and I will give you a complete account of the system, and expound the actual teachings of the great explorer of the truth, the master-builder of human happiness. No one rejects, dislikes, or avoids pleasure itself, because it is pleasure, but because those who do not know how to pursue pleasure rationally encounter consequences</p>
    <p>To take a trivial example, which of us ever undertakes laborious physical exercise, except to obtain</p>
  </div>
  <a class="btn btn-teal about-btn">Read More</a>
</section>

<section class="why" role="img" aria-label="Photo of a white and ruby lorry cab parked on a wet yard beside grass">
  <div class="why-box">
    <h2 class="section-title why-title">WHY CHOOSE US</h2>
    <p class="body-copy why-copy">I must explain to you how all this mistaken idea of denouncing pleasure and praising pain was born and I will give you a complete account of the system, and expound the actual teachings of the great explorer of the truth, the master-builder of human happiness. No one rejects, dislikes</p>
    <a class="btn btn-teal why-btn">Read More</a>
  </div>
</section>

<section>
  <h2 class="section-title news-title">READ THE LATEST NEWS</h2>
  <p class="news-sub">I must explain to you how all this mistaken idea of denouncing pleasure and praising pain was born and I will give you a complete account of the system, and expound the actual teachings</p>

  <div class="news-photo" style="left:105px;background:linear-gradient(160deg,#3d6f9e 0%,#9ab3c6 45%,#d98a4a 80%,#4b3a36 100%)" role="img" aria-label="Photo of a lorry in motion on a highway at sunrise"></div>
  <div class="news-photo" style="left:444px;background:linear-gradient(180deg,#5b6a8c 0%,#c98a86 50%,#e0a35a 70%,#2f2c36 100%)" role="img" aria-label="Photo of a lorry on an open road at dusk"></div>
  <div class="news-photo" style="left:781px;background:linear-gradient(180deg,#e8b56a 0%,#f2d7a8 45%,#d7c9b8 70%,#9c8e80 100%)" role="img" aria-label="Photo of white lorry cabs parked in warm sunlight"></div>

  <article class="news-card" style="left:118px">
    <div class="news-date">06/04/2024</div>
    <h3>SED UT PERSPICIATIS UNDE OMNIS ISTE NATUS ERROR SIT VOLUPTATEM</h3>
    <p>I must explain to you how all this mistaken idea of denouncing pleasure and praising pain was born and I will give you a complete account of the system</p>
  </article>
  <article class="news-card" style="left:456px">
    <div class="news-date">06/04/2024</div>
    <h3>SED UT PERSPICIATIS UNDE OMNIS ISTE NATUS ERROR SIT VOLUPTATEM</h3>
    <p>I must explain to you how all this mistaken idea of denouncing pleasure and praising pain was born and I will give you a complete account of the system</p>
  </article>
  <article class="news-card" style="left:794px">
    <div class="news-date">06/04/2024</div>
    <h3>SED UT PERSPICIATIS UNDE OMNIS ISTE NATUS ERROR SIT VOLUPTATEM</h3>
    <p>I must explain to you how all this mistaken idea of denouncing pleasure and praising pain was born and I will give you a complete account of the system</p>
  </article>
</section>

<section>
  <svg class="contact-wave" viewBox="0 0 1200 140" preserveAspectRatio="none" aria-hidden="true">
    <path d="M0,110 Q600,-40 1200,100 L1200,140 L0,140 Z" fill="#14978a"/>
    <path d="M0,128 Q600,-14 1200,118 L1200,140 L0,140 Z" fill="#1f1f27"/>
  </svg>
  <div class="contact"></div>
  <div class="contact-photo" role="img" aria-label="Photo of two white and ruby lorries parked side by side at night"></div>
  <h2 class="contact-title heading">GET IN TOUCH WITH US</h2>
  <div class="field" style="left:277px;top:3661px;width:310px;height:37px">Full Name</div>
  <div class="field" style="left:277px;top:3717px;width:310px;height:36px">Email Address</div>
  <div class="field" style="left:277px;top:3771px;width:310px;height:36px">Contact Number</div>
  <div class="send">Send Message</div>
  <div class="field" style="left:613px;top:3661px;width:311px;height:201px">Message</div>
</section>

<footer class="site-footer">
  <div class="footer-logo">Garvel Pryce<br>Transport</div>
  <p class="footer-about">I must explain to you how all this mistaken idea of denouncing pleasure and praising pain was born and I will give you</p>
  <div class="footer-col" style="left:438px">
    <h4>QUICK LINKS</h4>
    <ul><li>Home</li><li>About Us</li><li>Services</li><li>Why Choose Us</li><li>Blogs</li></ul>
  </div>
  <div class="footer-col" style="left:623px">
    <h4>HELP LINKS</h4>
    <ul><li>Help</li><li>Support</li><li>Privacy Policy</li><li>Terms Of Use</li></ul>
  </div>
  <div class="footer-col" style="left:796px">
    <h4>CONTACT US</h4>
    <ul><li>14 Harbour Road, Ferrowick,</li><li>FW4 2KT</li><li>&nbsp;</li><li>+1 555 014 2276</li><li>info@garvelpryce.com</li></ul>
  </div>
  <div class="footer-col" style="left:997px">
    <h4>FOLLOW US</h4>
    <ul><li>Newsfeed</li><li>Updates</li><li>Gallery</li><li>Video Channel</li></ul>
  </div>
</footer>
<div class="footer-rule"></div>
<div class="copyright">(C) COPYRIGHT 2024 | ALL RIGHTS RESERVED</div>

</body>
</html>
```